KTR Photography Editing & Support Services for Real Estate

We require a double sided A4 flyer to promote our photography services to real estate agencies.
This particular service is targeted to rural areas where reliable, professional and highly skilled photographers are difficult to source. We teach the agent how to photograph, they upload files to a server and we take care of the rest (image editing, quality control and delivery). This will give the agents flexibility with when to shoot and eliminates the stress of managing a photographer / contractor. We offer a 1 day face to face training session and competitive packages for equipment start up.
We would like the flyer to look clean & very professional. The flyer should showcase samples of our work to highlight what can be achieved by using our services. We like the look of a black or dark background behind the text and feel that would look nice with our photographs provided. Otherwise open to your suggestions and ideas.
TEXT FOR FLYER:
Welcome to the KTR Real Estate Photography Editing and Support Service
• Take your real estate business to the next level by providing impressive real estate imagery that makes you stands out from the competition
• Omit the stress of trying to find a good photographer or managing an unreliable one and hence have more time to focus on other aspects of your business
• Showcase your listings with better quality and more impactful photographs than your competitors thereby increasing potential for a quick sale
• Great first impressions matter and you will achieve this by looking and feeling more professional. This will attract and retain more future clients.
HOW IT WORKS
• We understand that your time is valuable, so let us handle the editing and delivery of your images. You shoot, and we take care of the rest.
• Images are edited and delivered within 1 working day
INCLUSIONS:
• Full day face to face training (we come to you) and instructional handbook
• We will teach you everything you need to know about your equipment and how to take stunning real estate photographs
• Service turnaround within 1 working day
• Free HELP desk service Mon-Fri
• 12 month Exclusivity (rural towns only) for a limited time
INVESTMENT
• 99 per listing for us to manage images including editing, quality control and delivery (10 Images)
• Ask us about competitive packages for photography equipment if required
SUMMARY
The KTR Real Estate Photography Editing and Support Service is the perfect solution for busy real estate professionals who want to take their business to the next level. Our service is affordable, flexible, and designed to help you showcase your listings in the best possible light.
Contact us today to learn more about how we can help you.

```html
<!DOCTYPE html>
<html lang="en">
<head>
<meta charset="utf-8">
<title>KTR Real Estate Photography Flyer</title>
<link href="https://fonts.googleapis.com/css2?family=Great+Vibes&family=Montserrat:wght@400;500;600;700&display=swap" rel="stylesheet">
<style>
:root{
  --ink:#0b0b0b;
  --paper:#ffffff;
  --mist:#dcdcdc;
  --stage:#8f908c;
  --text-light:#f2f2f2;
  --text-dark:#161616;
  --rule:#9a9a9a;
}
*{margin:0;padding:0;box-sizing:border-box}
html,body{width:792px;height:1200px;overflow:hidden}
body{background:var(--stage);font-family:"Montserrat",sans-serif;position:relative}
.sheet{position:absolute;top:337px;width:372px;height:526px;background:var(--mist);overflow:hidden;box-shadow:0 4px 10px rgba(0,0,0,.35)}
.sheet--front{left:12px}
.sheet--back{left:408px}
.abs{position:absolute}
.photo{position:absolute}
.band-black{position:absolute;left:0;width:100%;background:var(--ink)}

/* brand */
.brand{position:absolute;text-align:center;font-family:"Montserrat",sans-serif;font-weight:400;letter-spacing:.22em;text-transform:uppercase}
.sheet--front .brand{left:10px;top:36px;width:120px;font-size:8px;color:#b9bec6}
.sheet--back .brand{left:0;top:44px;width:187px;font-size:10px;color:#555}

/* front */
.hero{left:0;top:0;width:100%;height:184px;background:linear-gradient(115deg,#2c3340 0%,#5b6472 38%,#3a3f48 62%,#8a8f98 85%,#d7d9de 100%)}
.hero-rule{left:0;top:184px;width:100%;height:2px;background:var(--paper)}
.welcome{left:0;top:186px;width:100%;text-align:center;font-family:"Great Vibes",cursive;font-size:36px;color:var(--paper);line-height:1.2}
.headline{left:0;top:238px;width:100%;text-align:center;color:var(--paper);font-size:12.6px;font-weight:400;line-height:1.25;letter-spacing:.02em;text-transform:uppercase}
.benefits{left:0;top:285px;width:100%;height:100px}
.benefit{position:absolute;width:146px;color:var(--text-light);font-size:6.9px;line-height:1.28}
.benefit svg{position:absolute;left:-13px;top:0;width:8px;height:8px}
.col-rule{left:185px;top:285px;width:1px;height:93px;background:var(--text-light)}
.thumb{position:absolute;top:393px;height:75px;border:2px solid var(--paper)}

/* contact */
.contact-bar{position:absolute;left:0;top:476px;width:100%;height:14px;background:var(--ink);color:var(--paper);font-size:8px;text-align:center;line-height:14px}
.contact-bar b{font-weight:700}
.footer{position:absolute;left:0;top:490px;width:100%;height:36px;display:flex;align-items:center;justify-content:center;gap:6px;font-size:7px;color:var(--text-dark)}
.footer .studio{font-weight:700;margin-right:4px}
.footer .item{display:flex;align-items:center;gap:3px;font-weight:500}
.footer .phone{font-size:8px;font-weight:600}
.footer .sep{width:1px;height:11px;background:var(--text-dark)}
.footer svg{width:9px;height:9px}

/* back */
.side-photo{left:188px;top:0;width:184px;height:238px;background:linear-gradient(160deg,#eef0ee 0%,#c9b89a 30%,#7a5533 60%,#a9845a 80%,#d8cdb9 100%)}
.section-title{position:absolute;font-weight:600;font-size:12.5px;letter-spacing:.02em;text-transform:uppercase}
.dots{position:absolute;list-style:none;font-size:6.6px;line-height:1.25}
.dots li{position:relative;padding-left:14px}
.dots li::before{content:"";position:absolute;left:0;top:2px;width:4px;height:4px;border-radius:50%;background:currentColor}
.how{left:14px;top:108px;width:160px;color:var(--text-dark)}
.how li+li{margin-top:17px}
.interior{left:17px;top:187px;width:156px;height:111px;border:2px solid var(--paper);background:linear-gradient(180deg,#2a3b5c 0%,#5d7498 35%,#8a6d4c 60%,#c7b39a 100%)}
.summary-text{left:17px;top:331px;width:152px;color:var(--text-light);font-size:6.6px;line-height:1.22}
.inclusions{left:188px;top:279px;width:170px;color:var(--text-light)}
.inclusions li+li{margin-top:8px}
.invest-l{left:14px;top:439px;width:160px;color:var(--text-dark)}
.invest-r{left:199px;top:439px;width:160px;color:var(--text-dark)}
.invest-rule{left:187px;top:437px;width:1px;height:27px;background:var(--text-dark)}
</style>
</head>
<body>

<section class="sheet sheet--front">
  <div class="photo hero" role="img" aria-label="Living room interior with grey sofa, cushions, brass side table, floor lamp and sheer curtains casting window shadows"></div>
  <div class="abs hero-rule"></div>
  <div class="brand">Rhys Calder</div>

  <div class="band-black" style="top:186px;height:231px"></div>
  <div class="abs welcome">Welcome to the</div>
  <h1 class="abs headline">KTR Real Estate Photography<br>Editing and Support Service</h1>

  <div class="abs benefits">
    <p class="benefit" style="left:32px;top:0"><svg viewBox="0 0 10 10"><circle cx="5" cy="5" r="4.3" fill="none" stroke="#fff" stroke-width=".9"/><path d="M2.8 5.2l1.6 1.6 4.8-5" fill="none" stroke="#fff" stroke-width="1.2"/></svg>Take your real estate business to the next level by providing impressive real estate imagery that makes you stands out from the competition</p>
    <p class="benefit" style="left:32px;top:52px"><svg viewBox="0 0 10 10"><circle cx="5" cy="5" r="4.3" fill="none" stroke="#fff" stroke-width=".9"/><path d="M2.8 5.2l1.6 1.6 4.8-5" fill="none" stroke="#fff" stroke-width="1.2"/></svg>Showcase your listings with better quality and more impactful photographs than your competitors thereby increasing potential for a quick sale</p>
    <p class="benefit" style="left:213px;top:0"><svg viewBox="0 0 10 10"><circle cx="5" cy="5" r="4.3" fill="none" stroke="#fff" stroke-width=".9"/><path d="M2.8 5.2l1.6 1.6 4.8-5" fill="none" stroke="#fff" stroke-width="1.2"/></svg>Great first impressions matter and you will achieve this by looking and feeling more professional. This will attract and retain more future clients.</p>
    <p class="benefit" style="left:213px;top:52px"><svg viewBox="0 0 10 10"><circle cx="5" cy="5" r="4.3" fill="none" stroke="#fff" stroke-width=".9"/><path d="M2.8 5.2l1.6 1.6 4.8-5" fill="none" stroke="#fff" stroke-width="1.2"/></svg>Omit the stress of trying to find a good photographer or managing an unreliable one and hence have more time to focus on other aspects of your business</p>
  </div>
  <div class="abs col-rule"></div>

  <div class="thumb" style="left:15px;width:107px;background:linear-gradient(180deg,#f4f4f2 0%,#e2ddd4 50%,#a9784c 100%)" role="img" aria-label="Bright kitchen and dining room with timber floor"></div>
  <div class="thumb" style="left:132px;width:106px;background:linear-gradient(180deg,#eceef0 0%,#c4c9c6 40%,#7f8a6c 65%,#efefef 100%)" role="img" aria-label="Bedroom with large windows overlooking hills"></div>
  <div class="thumb" style="left:250px;width:106px;background:linear-gradient(180deg,#e9e4dd 0%,#d6cec3 55%,#b38a5e 78%,#ece9e5 100%)" role="img" aria-label="Bathroom with freestanding bath and timber vanity"></div>

  <div class="contact-bar"><b>Contact us today</b> to learn more about how we can help you.</div>
  <div class="footer">
    <span class="studio">Rhys Calder Photography :</span>
    <span class="item phone"><svg viewBox="0 0 10 10"><circle cx="5" cy="5" r="5" fill="#161616"/><path d="M3.2 2.6l1 1-.5.7c.4.8 1 1.4 1.8 1.8l.7-.5 1 1-.6.8C4.9 7.3 2.7 5.1 2.6 3.2z" fill="#fff"/></svg>61 400 555 019</span>
    <span class="sep"></span>
    <span class="item"><svg viewBox="0 0 10 10"><circle cx="5" cy="5" r="5" fill="#161616"/><rect x="2.6" y="3.3" width="4.8" height="3.4" fill="#fff"/><path d="M2.6 3.3L5 5.2l2.4-1.9" fill="none" stroke="#161616" stroke-width=".6"/></svg>shoot@rhyscalder.com.au</span>
  </div>
</section>

<section class="sheet sheet--back">
  <div class="photo side-photo" role="img" aria-label="Hallway with framed artworks on the wall, timber bench, cushions and a woven basket with a plant"></div>
  <div class="brand">Rhys Calder</div>

  <h2 class="section-title" style="left:14px;top:80px;color:var(--text-dark)">How it works</h2>
  <ul class="dots how">
    <li>We understand that your time is valuable, so let us handle the editing and delivery of your images. You shoot, and we take care of the rest.</li>
    <li>Images are edited and delivered within 1 working day</li>
  </ul>

  <div class="band-black" style="top:240px;height:168px"></div>
  <div class="band-black" style="top:238px;left:188px;width:184px;height:2px;background:var(--paper)"></div>
  <div class="photo interior" role="img" aria-label="Open living room with tall windows at dusk and a hanging fireplace"></div>

  <h2 class="section-title" style="left:17px;top:308px;color:var(--paper)">Summary</h2>
  <p class="abs summary-text">The KTR Real Estate Photography Editing and Support Service is the perfect solution for busy real estate professionals who want to take their business to the next level. Our service is affordable, flexible, and designed to help you showcase your listings in the best possible light.</p>

  <h2 class="section-title" style="left:188px;top:253px;color:var(--paper)">Inclusions:</h2>
  <ul class="dots inclusions">
    <li>Full day face to face training (we come to you) and instructional handbook</li>
    <li>We will teach you everything you need to know about your equipment and how to take stunning real estate photographs</li>
    <li>Service turnaround within 1 working day</li>
    <li>Free HELP desk service Mon-Fri</li>
    <li>12 month Exclusivity (rural towns only) for a limited time</li>
  </ul>

  <h2 class="section-title" style="left:0;top:416px;width:100%;text-align:center;color:var(--text-dark)">Investment</h2>
  <ul class="dots invest-l"><li>99 per listing for us to manage images including editing, quality control and delivery (10 Images)</li></ul>
  <div class="abs invest-rule"></div>
  <ul class="dots invest-r"><li>Ask us about competitive packages for photography equipment if required</li></ul>

  <div class="contact-bar"><b>Contact us today</b> to learn more about how we can help you.</div>
  <div class="footer">
    <span class="studio">Rhys Calder Photography :</span>
    <span class="item phone"><svg viewBox="0 0 10 10"><circle cx="5" cy="5" r="5" fill="#161616"/><path d="M3.2 2.6l1 1-.5.7c.4.8 1 1.4 1.8 1.8l.7-.5 1 1-.6.8C4.9 7.3 2.7 5.1 2.6 3.2z" fill="#fff"/></svg>61 400 555 019</span>
    <span class="sep"></span>
    <span class="item"><svg viewBox="0 0 10 10"><circle cx="5" cy="5" r="5" fill="#161616"/><rect x="2.6" y="3.3" width="4.8" height="3.4" fill="#fff"/><path d="M2.6 3.3L5 5.2l2.4-1.9" fill="none" stroke="#161616" stroke-width=".6"/></svg>shoot@rhyscalder.com.au</span>
  </div>
</section>

</body>
</html>
```